The Velvet Easel Co - Photos to Custom Oil Paintings

We need a website and logo designed and built allowing customers to purchase custom oil paintings. The paintings will come from a customers single photograph or even combination of photos. They will be able to complete a straight forward checkout process, selecting their desired medium (oil or charcoal painting), their desired size, the number of figures in the painting, the type of background required (as per photo or let the artist decide). Which will then automaticaly provide the customer with a price for the purchase. Allowing them to add a photo to the order which they can then submit with the order present in their personal account etc etc etc.
Theres one website in particular that i will be competing with. That is based in the US - http://www.brushmorrow.com
I wish to far exceed the appearence of the already present site.
At the moment i wish to include Coinvale in the payment process. Unless there are some cheaper, more cost efficient ways, please let me know.
The company name is The Velvet Easel Co. Domain has been purchased - www.thevelveteasel.co (via Hostlark - Linux)
I have no great sense of design, but the site must be straight forward, eye catching, engaging and give the customer a sense of high quality. Some kind of flash animation with pictures on the front page scrolling?
For myself, the admin side, ideally must be straight forward to maintain. The ability to update customers accounts with info (they will then be informed there is an update in their account etc)
The ability for automated emails from point of sale (sales orders with generated order numbers) to myself. Again automated emails to the customers once the "status" of their order or other information has been submitted to their account (by myself) or a similar system.
Updates
All,
Please note, the budget is able to increase subject to what additional work is needed. As far as the admin area goes. I am open to suggestions to ensure ease of use and efficiency.
Any questions, comments or ideas are fully welcomed.
Many thanks,
Dan Holloway
Industry/Entity Type
It Company
Logo Text
Logo styles of interest
Pictorial/Combination Logo
Abstract Logo
Wordmark Logo
Lettermark Logo
Look and feel
Each slider illustrates characteristics of the customer's brand and the style your logo design should communicate.

```html
<!DOCTYPE html>
<html lang="en">
<head>
<meta charset="utf-8">
<title>The Velvet Easel Co – Photos to Custom Oil Paintings</title>
<link rel="stylesheet" href="https://fonts.googleapis.com/css2?family=Cinzel:wght@400;600&family=Mali:wght@500;600&family=Pangolin&display=swap">
<style>
:root{
  --pink:#e3197a;
  --magenta:#cf0f62;
  --yellow:#ffd800;
  --lime:#95c827;
  --violet:#4e25a0;
  --navy:#17306f;
  --ink:#1a1a1a;
  --grey-bg:#f4f4f4;
  --line:#c8c8c8;
  --white:#ffffff;
  --art-a:#3a5fa8;
  --art-b:#c4563a;
  --photo-a:#c99a80;
  --photo-b:#8c5a48;
}
*{box-sizing:border-box;margin:0;padding:0}
html,body{width:1024px;height:1200px;overflow:hidden;background:var(--white)}
body{position:relative;font-family:"Mali",sans-serif;color:var(--ink)}
.abs{position:absolute}

.brand{left:14px;top:0;width:201px;height:180px;background:var(--white);box-shadow:0 2px 8px rgba(0,0,0,.18);z-index:2;display:flex;flex-direction:column;align-items:center;justify-content:center;gap:16px;padding-top:20px}
.brand-mark{width:18px;height:18px;background:var(--magenta)}
.brand-name{font-family:"Cinzel",serif;font-size:20px;letter-spacing:.5px;color:var(--ink);text-align:center;line-height:1.2;white-space:nowrap}

.utility{right:20px;top:28px;display:flex;gap:18px}
.utility a{display:flex;flex-direction:column;align-items:center;gap:6px;font-size:11px;font-weight:600;color:var(--navy);text-decoration:none}
.utility svg{width:40px;height:38px}
.cards{right:18px;top:99px;display:flex;gap:3px}
.card{width:36px;height:22px;border:1px solid var(--line);border-radius:2px;background:#eef1f7;font-size:6px;font-weight:600;color:var(--navy);display:flex;align-items:center;justify-content:center;text-align:center;line-height:1}

.nav{left:215px;top:125px;width:797px;height:55px;background:var(--pink);display:flex;align-items:center;padding-left:35px;gap:20px}
.nav a{font-family:"Cinzel",serif;font-size:13.5px;color:var(--white);text-decoration:none;text-shadow:0 1px 1px rgba(0,0,0,.35)}

.hero{left:20px;top:195px;width:984px;height:393px;background:var(--yellow)}
.quote-mark{font-family:Georgia,serif;font-size:80px;color:var(--white);line-height:1}
.hero-title{left:48px;top:138px;width:420px;font-family:"Pangolin",cursive;font-size:30px;letter-spacing:-.6px;line-height:43px;color:var(--white);text-shadow:1px 2px 2px rgba(0,0,0,.25)}
.hero-sub{left:48px;top:232px;width:380px;font-family:"Cinzel",serif;font-weight:600;font-size:17px;line-height:21px;color:var(--navy)}
.hero-link{left:50px;top:286px;font-family:"Pangolin",cursive;font-size:21px;color:var(--ink);text-decoration:none}
.frame{background:var(--white);padding:8px}
.frame div{width:100%;height:100%}
.art-fill{background:linear-gradient(135deg,var(--art-b),var(--art-a) 45%,#2bb6a8 70%,var(--art-b))}
.photo-fill{background:linear-gradient(135deg,var(--photo-a),#e8c9b6 50%,var(--photo-b))}
.hero-shadow{left:30px;top:590px;width:964px;height:30px;background:radial-gradient(ellipse at top,rgba(0,0,0,.16),rgba(0,0,0,0) 70%)}

.welcome{left:14px;top:635px;width:1000px;height:313px;background:var(--grey-bg)}
.welcome h2{position:absolute;left:31px;top:38px;font-family:"Cinzel",serif;font-weight:400;font-size:20px;color:var(--ink)}
.welcome-copy{position:absolute;left:31px;top:82px;width:218px;font-size:9.5px;letter-spacing:-.3px;line-height:16.5px;color:var(--navy);font-weight:600}
.perks{position:absolute;left:31px;top:162px;list-style:none;font-size:10px;letter-spacing:-.2px;font-weight:600;color:var(--pink)}
.perks li{height:30px}
.slider{position:absolute;left:265px;top:18px;width:709px;height:220px;border:1px solid var(--line);border-radius:14px;background:#fbfbfb;overflow:hidden}
.thumb{position:absolute;top:20px;width:172px;height:170px}
.scroll-track{position:absolute;left:504px;top:271px;width:250px;height:6px;border-radius:3px;background:linear-gradient(#ddd,#999)}
.scroll-thumb{position:absolute;left:100px;top:-1px;width:50px;height:8px;border-radius:4px;background:var(--white);border:1px solid #aaa}

.promo{left:12px;top:970px;width:1000px;height:124px}
.promo svg{position:absolute;inset:0}
.promo-text{position:absolute;color:var(--white);font-family:"Mali",sans-serif;font-weight:600;font-size:12px;line-height:17px}
.slogan{font-size:11px;line-height:16px;white-space:nowrap;transform-origin:left top}
.testimonial-label{left:588px;top:76px;font-size:15px}
.testimonial{left:699px;top:46px;width:285px;font-size:10px;line-height:14px;font-weight:500}

.copyright{right:18px;top:1118px;font-size:10px;font-weight:600;color:var(--ink)}
</style>
</head>
<body>

<header>
  <div class="brand abs">
    <span class="brand-mark"></span>
    <span class="brand-name">The Velvet Easel</span>
  </div>

  <div class="utility abs">
    <a href="#">
      <svg viewBox="0 0 40 38" aria-hidden="true"><circle cx="20" cy="15" r="11" fill="#e4eef6" stroke="#b9c9d6"/><path d="M13 24l-4 12 7-4 3 5 1-11M27 24l4 12-7-4-3 5" fill="#e4eef6" stroke="#b9c9d6"/></svg>
      Guarantee
    </a>
    <a href="#">
      <svg viewBox="0 0 40 38" aria-hidden="true"><rect x="4" y="9" width="32" height="22" rx="2" fill="#eaf2f8" stroke="#b9c9d6"/><path d="M4 10l16 12 16-12" fill="none" stroke="#b9c9d6"/></svg>
      Contact us
    </a>
  </div>

  <div class="cards abs">
    <span class="card">Veltra<br>Debit</span>
    <span class="card">Amstead</span>
    <span class="card">Disclay</span>
    <span class="card">Meridi</span>
    <span class="card">Coinvale</span>
    <span class="card">Veltra</span>
  </div>

  <nav class="nav abs">
    <a href="#">How It Works</a>
    <a href="#">Order Your Painting</a>
    <a href="#">Galleries</a>
    <a href="#">Gift ideas</a>
    <a href="#">Testimonials</a>
    <a href="#">FAQ</a>
    <a href="#">Prices</a>
  </nav>
</header>

<section class="hero abs">
  <span class="quote-mark abs" style="left:6px;top:118px">“</span>
  <span class="quote-mark abs" style="left:362px;top:104px">”</span>
  <p class="hero-title abs">Your story happens on the go and so do we!</p>
  <p class="hero-sub abs">The Velvet Easel makes it easy to share your photos anywhere.</p>
  <a class="hero-link abs" href="#">find out here</a>
  <div class="frame abs" style="left:494px;top:40px;width:258px;height:250px">
    <div class="art-fill" role="img" aria-label="Colourful painted group of figures"></div>
  </div>
  <div class="frame abs" style="left:708px;top:113px;width:258px;height:250px">
    <div class="photo-fill" role="img" aria-label="Photo of two children sharing a snack"></div>
  </div>
</section>
<div class="hero-shadow abs"></div>

<section class="welcome abs">
  <h2>Welcome</h2>
  <p class="welcome-copy">thevelveteasel.co is the world leader in Photo to Painting services. Our portrait painters will create a 100% Handmade work of art as a perfect gift for your loved ones.</p>
  <ul class="perks">
    <li>•Real Live Painters</li>
    <li>•Affordable Prices</li>
    <li>•Quick Turnaround</li>
    <li>•Free Photo Editing</li>
  </ul>
  <div class="slider">
    <div class="thumb art-fill" style="left:26px" role="img" aria-label="Gallery painting of figures in bright colours"></div>
    <div class="thumb art-fill" style="left:216px" role="img" aria-label="Gallery painting of figures in bright colours"></div>
    <div class="thumb art-fill" style="left:406px" role="img" aria-label="Gallery painting of figures in bright colours"></div>
    <div class="thumb art-fill" style="left:596px;width:78px" role="img" aria-label="Gallery painting of figures in bright colours"></div>
  </div>
  <div class="scroll-track"><div class="scroll-thumb"></div></div>
</section>

<section class="promo abs">
  <svg width="1000" height="124" viewBox="0 0 1000 124" aria-hidden="true">
    <rect width="1000" height="124" fill="var(--violet)"/>
    <polygon points="0,0 778,0 398,124 0,124" fill="var(--lime)"/>
    <polygon points="0,0 378,0 0,124" fill="var(--magenta)"/>
  </svg>
  <span class="promo-text slogan" style="left:18px;top:84px;transform:rotate(-22deg)">Let Us Paint Your Life!</span>
  <span class="promo-text slogan" style="left:348px;top:84px;transform:rotate(-20deg)">Print Your Favorite Picture On Canvas in a<br>Style of Your Choice</span>
  <span class="promo-text testimonial-label">Testimonial</span>
  <p class="promo-text testimonial">"Thank you so much! My husband and I loved the photo of my daughter turned to pop art. It looks great in my daughters room."<br>Marla Penwick, Nov-14-2011</p>
</section>

<footer class="copyright abs">Copyright © thevelveteasel.co.</footer>

</body>
</html>
```